business card deign

Logo needs the following on it.
1. attached logo
2. Tagline - "From chilled coolers to backyard fun...we bring it all!"
3. Name- Dalton Pikes, Founder and CPO
4. Address - 412 E. Carver Avenue, Ste 2207, Tampa, FL. 33917
5. Phone - 555.318.4726

```html
<!DOCTYPE html>
<html lang="en">
<head>
<meta charset="utf-8">
<title>Hopwell Business Card</title>
<link href="https://fonts.googleapis.com/css2?family=Raleway:wght@700&family=Roboto:wght@400;700&display=swap" rel="stylesheet">
<style>
  :root {
    --stage: #232323;
    --card-dark: #1d1d1d;
    --card-dark-mark: #0e0e0e;
    --paper: #ffffff;
    --ink: #111111;
    --muted: #6f6f6f;
    --rule: #9a9a9a;
    --band: #0b0b0b;
    --band-text: #ffffff;
  }
  * { box-sizing: border-box; margin: 0; padding: 0; }
  html, body {
    width: 1200px; height: 825px; overflow: hidden;
    background: var(--stage);
  }
  .stage {
    width: 1200px; height: 825px;
    display: flex; align-items: center; justify-content: center; gap: 48px;
  }
  .card {
    width: 540px; height: 309px; position: relative; overflow: hidden;
    box-shadow: 0 14px 30px rgba(0,0,0,.45);
  }

  /* Back side */
  .card--back { background: var(--card-dark); display: flex; align-items: center; justify-content: center; }
  .card--back .wordmark {
    font-family: "Roboto", sans-serif; font-weight: 700;
    font-size: 58px; letter-spacing: 14px; color: var(--card-dark-mark);
    text-transform: uppercase;
  }

  /* Front side */
  .card--front { background: var(--paper); }
  .brand {
    position: absolute; left: 0; top: 0; width: 255px; height: 238px;
    display: flex; align-items: center; justify-content: center;
  }
  .brand .wordmark {
    font-family: "Roboto", sans-serif; font-weight: 700;
    font-size: 28px; letter-spacing: 8px; color: var(--ink);
    text-transform: uppercase;
  }
  .divider {
    position: absolute; left: 255px; top: 40px; width: 1px; height: 165px;
    background: linear-gradient(var(--paper), var(--rule) 30%, var(--rule) 70%, var(--paper));
  }
  .details {
    position: absolute; left: 282px; top: 44px; right: 20px;
    font-family: "Roboto", sans-serif; color: var(--muted); font-size: 12.5px; line-height: 1.35;
  }
  .details .person {
    font-family: "Raleway", sans-serif; font-weight: 700; font-size: 17px;
    color: var(--ink); text-transform: uppercase; letter-spacing: .3px;
  }
  .details .role { margin-bottom: 12px; }
  .details .address { margin-bottom: 10px; }
  .contact { list-style: none; }
  .contact li { display: flex; align-items: center; gap: 7px; }
  .contact svg { width: 11px; height: 11px; fill: var(--ink); flex: none; }
  .tagline-band {
    position: absolute; left: 0; right: 0; top: 238px; height: 38px;
    background: var(--band); display: flex; align-items: center; justify-content: center;
    font-family: "Roboto", sans-serif; font-size: 14px; color: var(--band-text);
  }
</style>
</head>
<body>
  <main class="stage">
    <section class="card card--back" aria-label="Card back">
      <span class="wordmark">Hopwell</span>
    </section>

    <section class="card card--front" aria-label="Card front">
      <div class="brand"><span class="wordmark">Hopwell</span></div>
      <div class="divider"></div>
      <div class="details">
        <p class="person">Dalton Pikes</p>
        <p class="role">Founder and CPO</p>
        <p class="address">412 E. Carver Avenue,<br>Ste 2207, Tampa, FL. 33917</p>
        <ul class="contact">
          <li>
            <svg viewBox="0 0 16 16" aria-hidden="true"><path d="M2 6c0-2 2-3 6-3s6 1 6 3v1h-3V5.5H5V7H2z M4 8h8l1 6H3z"/></svg>
            555.318.4726
          </li>
          <li>
            <svg viewBox="0 0 16 16" aria-hidden="true"><path d="M1 3h14v1.5L8 9 1 4.5z M1 6.5l7 4.5 7-4.5V13H1z"/></svg>
            info@daltonpikes.com
          </li>
        </ul>
      </div>
      <div class="tagline-band">From chilled coolers to backyard fun...we bring it all!</div>
    </section>
  </main>
</body>
</html>
```